Calloway needs a modernized design

We would like a modern update (that can be responsive) to our existing website. Attached are the two existing pages we would like new concepts of - our home page and a page about one of our locations.

Calloway is provides executive offices and virtual office services. Startups, law firms, and financial services are our primary clients. We would like a professional, clean design, leaning towards minimalist. We intend to greatly reduce/eliminate the long paragraphs of text.

Requirements
Must have
• A design that can be responsive
Nice to have
• Large image(s) on home page that rotate.

```html
<!DOCTYPE html>
<html lang="en">
<head>
<meta charset="utf-8">
<title>Calloway Business Centers</title>
<link rel="stylesheet" href="https://fonts.googleapis.com/css2?family=Cinzel:wght@400;700&family=Lato:wght@400;700&display=swap">
<style>
:root{
  --navy:#263a72;
  --navy-deep:#1f3264;
  --orange:#f39322;
  --orange-deep:#e6841a;
  --ink:#444b58;
  --grey-bg:#e9e9e9;
  --grey-light:#f1f1f1;
  --rule:#c9ccd3;
  --white:#ffffff;
  --red:#d23a2c;
  --sky:#2e9fd8;
  --blue:#1d6fa8;
}
*{box-sizing:border-box;margin:0;padding:0}
html,body{width:1200px;height:2769px;overflow:hidden}
body{font-family:"Lato",Arial,sans-serif;color:var(--ink);background:var(--white);position:relative}
.abs{position:absolute}
.serif{font-family:"Cinzel",Georgia,serif}

/* header */
.site-header{position:absolute;left:0;top:0;width:1200px;height:111px;background:var(--white);border-top:3px solid var(--navy)}
.brand{position:absolute;left:61px;top:18px;display:flex;align-items:center;gap:12px}
.brand-dot{width:74px;height:74px;border-radius:50%;background:var(--navy)}
.brand-name{font-family:"Cinzel",Georgia,serif;color:var(--navy);font-size:36px;line-height:1;font-weight:700}
.brand-name small{display:block;font-size:15px;letter-spacing:2px;font-weight:700;margin-top:4px}
.social-top{position:absolute;left:824px;top:9px;display:flex;gap:8px}
.social-top span{width:24px;height:24px;border-radius:50%}
.phone-pill{position:absolute;left:978px;top:0;width:222px;height:34px;background:var(--navy);border-bottom-left-radius:30px;color:var(--white);font-size:19px;display:flex;align-items:center;gap:10px;padding-left:40px}
.main-nav{position:absolute;left:472px;top:68px;display:flex;align-items:center;font-family:"Cinzel",Georgia,serif;font-weight:700;font-size:16px;color:var(--navy)}
.main-nav a{color:inherit;text-decoration:none;padding:0 15px;border-left:1px solid var(--rule)}
.main-nav a:first-of-type{border-left:none}
.main-nav .home{margin-right:10px}

/* hero */
.hero{position:absolute;left:0;top:111px;width:1200px;height:507px;background:linear-gradient(120deg,#6f7f93 0%,#c5d3e0 35%,#9fb3c6 60%,#3e4656 100%)}
.hero-caption{position:absolute;left:0;bottom:0;width:1200px;height:56px;background:rgba(20,24,34,.72);color:var(--white);font-size:35px;text-align:center;line-height:56px;letter-spacing:.5px}
.hero-arrow{position:absolute;top:352px;width:28px;height:44px;background:rgba(255,255,255,.85);display:flex;align-items:center;justify-content:center}
.hero-arrow.left{left:0;border-radius:0 22px 22px 0}
.hero-arrow.right{right:0;border-radius:22px 0 0 22px}

/* welcome */
.welcome{position:absolute;left:0;top:618px;width:1200px;height:390px;text-align:center}
.section-title{font-family:"Cinzel",Georgia,serif;color:var(--navy);font-size:40px;letter-spacing:1px;font-weight:400}
.divider{position:relative;margin:12px auto 0;width:450px;height:26px}
.divider::before{content:"";position:absolute;left:0;right:0;top:13px;border-top:1px solid var(--rule)}
.divider span{position:absolute;left:212px;top:0;width:26px;height:26px;border-radius:50%;background:var(--navy);border:3px solid var(--white);box-shadow:0 0 0 1px var(--rule)}
.welcome .section-title{margin-top:38px}
.welcome-lead{margin:30px auto 0;width:1020px;font-weight:700;color:var(--navy);font-size:19px;line-height:27px}
.welcome-body{margin:22px auto 0;width:1080px;font-size:14.5px;line-height:23px;color:#555}
.btn{display:inline-flex;align-items:center;gap:8px;height:32px;padding:0 16px 0 4px;border-radius:16px;font-size:14px;font-weight:700;color:var(--white);text-decoration:none}
.btn .dot{width:26px;height:26px;border-radius:50%;background:var(--navy)}
.btn-orange{background:var(--orange)}
.btn-orange .dot{background:var(--navy)}
.btn-navy{background:var(--navy)}
.btn-navy .dot{background:var(--white)}
.welcome .btn{margin-top:24px}

/* offer panels */
.offers{position:absolute;left:0;top:1008px;width:1200px;height:463px}
.offer{position:absolute;top:0;height:463px;width:600px}
.offer.exec{left:0;background:linear-gradient(135deg,#35477f 0%,var(--navy) 55%,#2a3d73 100%)}
.offer.virtual{left:600px;background:linear-gradient(135deg,#f7a33c 0%,var(--orange) 55%,#ee8c1d 100%)}
.notch{position:absolute;left:570px;top:0}
.link-line{position:absolute;left:308px;top:121px;width:584px;border-top:2px solid rgba(255,255,255,.5)}
.link-line::before,.link-line::after{content:"";position:absolute;top:-6px;width:10px;height:10px;border-radius:50%;background:#cfd5e4}
.link-line::before{left:96px}.link-line::after{right:96px}
.center-seal{position:absolute;left:558px;top:80px;width:84px;height:84px;border-radius:50%;background:var(--white);border:5px solid var(--navy);box-shadow:0 0 0 4px var(--white)}
.icon-ring{position:absolute;top:58px;width:128px;height:128px;border-radius:50%;display:flex;align-items:center;justify-content:center;border:4px solid rgba(255,255,255,.9)}
.exec .icon-ring{left:244px;background:var(--orange)}
.virtual .icon-ring{left:242px;background:var(--navy)}
.offer h2{position:absolute;top:200px;left:0;width:600px;text-align:center;font-family:"Cinzel",Georgia,serif;font-weight:400;font-size:33px;letter-spacing:1px}
.exec h2{color:var(--orange)}
.virtual h2{color:var(--white)}
.checks{position:absolute;top:267px;list-style:none;display:grid;grid-template-columns:auto auto;column-gap:30px;row-gap:11px;font-size:14px;font-weight:700;color:var(--white)}
.exec .checks{left:110px}
.virtual .checks{left:106px}
.checks li{display:flex;align-items:center;gap:9px}
.checks svg{flex:none}
.offer .btn{position:absolute;top:377px}
.exec .btn{left:236px}
.virtual .btn{left:232px}

/* community / services */
.community{position:absolute;left:0;top:1471px;width:596px;height:554px;background:linear-gradient(90deg,var(--white) 0%,var(--grey-light) 60%,var(--grey-bg) 100%)}
.services{position:absolute;left:596px;top:1471px;width:604px;height:554px;background:var(--grey-light)}
.block-title{position:absolute;top:52px;font-family:"Cinzel",Georgia,serif;color:var(--navy);font-size:33px;font-weight:400;letter-spacing:1px}
.community .block-title{left:61px}
.services .block-title{left:45px}
.community-photo{position:absolute;left:61px;top:131px;width:489px;height:203px;background:linear-gradient(135deg,#8a5a3a 0%,#c89a72 45%,#a36b44 100%)}
.community-text{position:absolute;left:61px;top:348px;width:490px;font-size:13.5px;line-height:21.5px;color:#4a4a4a}
.read-link{font-size:14px;font-weight:700;color:var(--navy);text-decoration:none}
.community .read-link{position:absolute;left:64px;top:487px}
.service{position:absolute;left:45px;width:500px;height:124px;border-bottom:1px dashed #a9acb4}
.service:last-of-type{border-bottom:none}
.service .ico{position:absolute;left:0;top:0;width:62px;height:62px;border-radius:50%;background:#2b2b2b;display:flex;align-items:center;justify-content:center}
.service h3{position:absolute;left:75px;top:-2px;color:var(--orange);font-size:20px;font-weight:700}
.service p{position:absolute;left:75px;top:28px;width:425px;font-size:13px;line-height:19px;color:#444}
.service .read-link{position:absolute;left:75px;top:72px;font-size:13.5px}

/* partners */
.partners{position:absolute;left:0;top:2025px;width:1200px;height:300px;background:var(--white);text-align:center}
.partners .section-title{margin-top:51px;font-size:36px}
.partner-row{position:absolute;left:61px;top:170px;display:flex;gap:27px}
.partner{width:157px;height:74px;border:1px solid #cfd2d8;display:flex;align-items:center;justify-content:center}
.partner span{width:100px;height:24px;border-radius:4px;background:#d6d8dd}
.partner-arrow{position:absolute;top:190px}

/* footer */
.site-footer{position:absolute;left:0;top:2325px;width:1200px;height:444px}
.footer-curve{position:absolute;left:0;top:0}
.footer-seal{position:absolute;left:556px;top:-10px;width:88px;height:88px;border-radius:50%;background:var(--white);border:5px solid var(--navy);box-shadow:0 0 0 5px var(--white)}
.footer-col{position:absolute;top:140px}
.footer-col h4{font-family:"Cinzel",Georgia,serif;font-weight:400;color:var(--white);font-size:21px;letter-spacing:1px}
.footer-col h4::after{content:"";display:block;width:190px;margin-top:12px;border-top:1px solid rgba(255,255,255,.2)}
.quick-links{left:61px}
.quick-links ul{list-style:none;margin-top:16px}
.quick-links li{color:#dfe4f0;font-size:13.5px;height:35px;display:flex;align-items:center;gap:12px}
.quick-links li::before{content:"";width:5px;height:5px;border-radius:50%;background:var(--orange)}
.contact-col{left:310px}
.contact-col ul{list-style:none;margin-top:16px;color:#dfe4f0;font-size:13.5px;line-height:20px}
.contact-col li{display:flex;gap:12px;margin-bottom:14px}
.contact-col li svg{flex:none;margin-top:2px}
.contact-col strong{color:var(--white)}
.form-col{left:642px}
.form-col form{margin-top:18px;width:280px}
.field{display:block;width:277px;height:37px;margin-bottom:8px;background:var(--white);border:none;border-radius:3px;padding:0 10px;font-family:"Lato",Arial,sans-serif;font-size:13px;color:#888;line-height:37px}
.submit{display:block;width:130px;height:37px;margin-top:14px;background:#3d5aa8;color:var(--white);font-weight:700;font-size:15px;text-align:center;line-height:37px;border-radius:2px}
.follow-col{left:1017px}
.follow-col h4::after{width:120px}
.follow-col ul{list-style:none;margin-top:26px}
.follow-col li{display:flex;align-items:center;gap:12px;height:45px;color:var(--white);font-size:13.5px;font-weight:700;letter-spacing:.5px}
.follow-col li span{width:31px;height:31px;border-radius:50%}
.col-sep{position:absolute;top:140px;height:270px;border-left:1px solid rgba(255,255,255,.15)}
.copyright{position:absolute;left:0;top:398px;width:1200px;height:46px;background:var(--orange);color:var(--white);font-size:13.5px;font-weight:700;text-align:center;line-height:46px}
</style>
</head>
<body>

<header class="site-header">
  <div class="brand"><span class="brand-dot"></span><div class="brand-name">Calloway<small>Business Centers</small></div></div>
  <div class="social-top"><span style="background:var(--red)"></span><span style="background:var(--blue)"></span><span style="background:var(--sky)"></span><span style="background:#d24a36"></span></div>
  <div class="phone-pill">
    <svg width="18" height="18" viewBox="0 0 24 24"><path d="M6.6 10.8a15 15 0 0 0 6.6 6.6l2.2-2.2a1 1 0 0 1 1-.25 11.4 11.4 0 0 0 3.6.57 1 1 0 0 1 1 1V20a1 1 0 0 1-1 1A17 17 0 0 1 3 4a1 1 0 0 1 1-1h3.5a1 1 0 0 1 1 1c0 1.25.2 2.45.57 3.6a1 1 0 0 1-.25 1z" fill="#fff"/></svg>
    + 214.555.0147
  </div>
  <nav class="main-nav">
    <svg class="home" width="28" height="28" viewBox="0 0 24 24"><path d="M12 3 2 12h3v9h5v-6h4v6h5v-9h3z" fill="var(--navy)"/></svg>
    <a>Properties</a><a>Virtual Tours &amp; Videos</a><a>Photos</a><a>Broker Referrals</a>
  </nav>
</header>

<section class="hero" role="img" aria-label="Rotating banner photo: a presenter at a whiteboard with colleagues in a bright office meeting room">
  <div class="hero-arrow left"><svg width="12" height="16" viewBox="0 0 12 16"><path d="M9 2 3 8l6 6" stroke="#333" stroke-width="2.5" fill="none"/></svg></div>
  <div class="hero-arrow right"><svg width="12" height="16" viewBox="0 0 12 16"><path d="m3 2 6 6-6 6" stroke="#333" stroke-width="2.5" fill="none"/></svg></div>
  <div class="hero-caption">We Provide Executive Offices And Virtual Office Services</div>
</section>

<section class="welcome">
  <h1 class="section-title">Welcome to Calloway Business Centers</h1>
  <div class="divider"><span></span></div>
  <p class="welcome-lead">Come See Why Smarter Companies are Choosing Calloway Business Centers' Dallas, Ft. Worth and Houston Executive Office Suites, Virtual Offices, Meeting Rooms and Video Conferencing.</p>
  <p class="welcome-body">Either you need Dallas/Ft. Worth Office Space, Dallas Executive Suites, Ft. Worth Executive Suites, Houston Office Space, Houston Executive Suites, or maybe you simply need a place to stop in and use an on-demand office or meeting room from time to time or utilize our local business phone numbers, phone answering or business addresses through one of our virtual office solutions</p>
  <a class="btn btn-orange"><span class="dot"></span>Read More &raquo;</a>
</section>

<section class="offers">
  <div class="offer exec">
    <div class="icon-ring">
      <svg width="60" height="60" viewBox="0 0 60 60" fill="none" stroke="#fff" stroke-width="3"><rect x="18" y="6" width="24" height="24" rx="4"/><path d="M12 34h36M30 34v12M18 52l12-6 12 6M18 52v2M42 52v2"/></svg>
    </div>
    <h2>Executive Offices</h2>
    <ul class="checks">
      <li><svg width="12" height="12" viewBox="0 0 12 12"><rect width="12" height="12" rx="2" fill="var(--orange)"/><path d="m3 6 2 2 4-4" stroke="#fff" stroke-width="1.6" fill="none"/></svg>Full Service Offices</li>
      <li><svg width="12" height="12" viewBox="0 0 12 12"><rect width="12" height="12" rx="2" fill="var(--orange)"/><path d="m3 6 2 2 4-4" stroke="#fff" stroke-width="1.6" fill="none"/></svg>Flexible Contracts from $395</li>
      <li><svg width="12" height="12" viewBox="0 0 12 12"><rect width="12" height="12" rx="2" fill="var(--orange)"/><path d="m3 6 2 2 4-4" stroke="#fff" stroke-width="1.6" fill="none"/></svg>Disaster Recovery</li>
      <li><svg width="12" height="12" viewBox="0 0 12 12"><rect width="12" height="12" rx="2" fill="var(--orange)"/><path d="m3 6 2 2 4-4" stroke="#fff" stroke-width="1.6" fill="none"/></svg>Corporate or Satellite Offices</li>
      <li><svg width="12" height="12" viewBox="0 0 12 12"><rect width="12" height="12" rx="2" fill="var(--orange)"/><path d="m3 6 2 2 4-4" stroke="#fff" stroke-width="1.6" fill="none"/></svg>All-Inclusive Pricing!</li>
    </ul>
    <a class="btn btn-orange"><span class="dot"></span>Read More &raquo;</a>
  </div>
  <div class="offer virtual">
    <div class="icon-ring">
      <svg width="64" height="60" viewBox="0 0 64 60" fill="none" stroke="#fff" stroke-width="3"><rect x="30" y="10" width="26" height="20" rx="2"/><path d="M43 30v6M6 40h52M10 40v16M54 40v16"/><circle cx="18" cy="16" r="6"/><path d="M10 38v-8a8 8 0 0 1 16 0v8"/></svg>
    </div>
    <h2>Virtual Office</h2>
    <ul class="checks">
      <li><svg width="12" height="12" viewBox="0 0 12 12"><rect width="12" height="12" rx="2" fill="var(--navy)"/><path d="m3 6 2 2 4-4" stroke="#fff" stroke-width="1.6" fill="none"/></svg>Mailing Address $49/mo</li>
      <li><svg width="12" height="12" viewBox="0 0 12 12"><rect width="12" height="12" rx="2" fill="var(--navy)"/><path d="m3 6 2 2 4-4" stroke="#fff" stroke-width="1.6" fill="none"/></svg>Flexible Contracts</li>
      <li><svg width="12" height="12" viewBox="0 0 12 12"><rect width="12" height="12" rx="2" fill="var(--navy)"/><path d="m3 6 2 2 4-4" stroke="#fff" stroke-width="1.6" fill="none"/></svg>Local Phone &amp; Mail $99/mo</li>
      <li><svg width="12" height="12" viewBox="0 0 12 12"><rect width="12" height="12" rx="2" fill="var(--navy)"/><path d="m3 6 2 2 4-4" stroke="#fff" stroke-width="1.6" fill="none"/></svg>All-Inclusive Pricing!</li>
      <li><svg width="12" height="12" viewBox="0 0 12 12"><rect width="12" height="12" rx="2" fill="var(--navy)"/><path d="m3 6 2 2 4-4" stroke="#fff" stroke-width="1.6" fill="none"/></svg>Corporate or Satellite Offices</li>
    </ul>
    <a class="btn btn-navy"><span class="dot"></span>Read More &raquo;</a>
  </div>
  <svg class="notch" width="60" height="20" viewBox="0 0 60 20"><path d="M0 0h60L30 18z" fill="var(--white)"/></svg>
  <div class="link-line"></div>
  <div class="center-seal"></div>
</section>

<section class="community">
  <h2 class="block-title">Community</h2>
  <div class="community-photo" role="img" aria-label="Photo of many hands stacked together over a wooden table, showing teamwork"></div>
  <p class="community-text">Lorem ipsum dolor sit amet, consectetuer adipiscing elit, sed diam nonummy nibh euismod tincidunt ut laoreet dolore magna aliquam erat volutpat. Ut wisi enim ad minim veniam, quis nostrud exerci tation ullamcorper suscipit lobortis nisl utiquip ex ea commodo consequat. Duis autem vel eum iriure dolor in hendrerit inputate velit esse molestie consequat, vel illum dolore eu feugiat nulla facilisis at vero eros et accumsan et iusto odio dignissim qui blandit</p>
  <a class="read-link">Read More &raquo;</a>
</section>

<section class="services">
  <h2 class="block-title">Other Services</h2>
  <div class="service" style="top:144px">
    <div class="ico"><svg width="36" height="36" viewBox="0 0 36 36" fill="#fff"><rect x="10" y="13" width="16" height="10" rx="2"/><circle cx="6" cy="18" r="3"/><circle cx="30" cy="18" r="3"/><circle cx="14" cy="8" r="3"/><circle cx="22" cy="8" r="3"/><circle cx="14" cy="28" r="3"/><circle cx="22" cy="28" r="3"/></svg></div>
    <h3>On-demand Meeting Rooms</h3>
    <p>Lorem ipsum dolor sit amet, consectetuer adipiscing elit, sed diam my nibh euismod dloer sknev cjsrewvc bnarv bdivrt.</p>
    <a class="read-link">Read More &raquo;</a>
  </div>
  <div class="service" style="top:281px">
    <div class="ico"><svg width="36" height="36" viewBox="0 0 36 36" fill="#fff"><circle cx="18" cy="18" r="7"/><circle cx="18" cy="5" r="3"/><circle cx="18" cy="31" r="3"/><circle cx="5" cy="18" r="3"/><circle cx="31" cy="18" r="3"/><circle cx="9" cy="9" r="2.5"/><circle cx="27" cy="9" r="2.5"/><circle cx="9" cy="27" r="2.5"/><circle cx="27" cy="27" r="2.5"/></svg></div>
    <h3>On-demand Training Rooms</h3>
    <p>Lorem ipsum dolor sit amet, consectetuer adipiscing elit, sed diam my nibh euismod dloer sknev cjsrewvc bnarv bdivrt.</p>
    <a class="read-link">Read More &raquo;</a>
  </div>
  <div class="service" style="top:418px">
    <div class="ico"><svg width="36" height="36" viewBox="0 0 36 36" fill="#fff"><circle cx="18" cy="10" r="5"/><path d="M9 24a9 9 0 0 1 18 0z"/><circle cx="7" cy="15" r="3"/><circle cx="29" cy="15" r="3"/><rect x="4" y="26" width="28" height="4" rx="1"/></svg></div>
    <h3>Virtual Office Solutions</h3>
    <p>Lorem ipsum dolor sit amet, consectetuer adipiscing elit, sed diam my nibh euismod dloer sknev cjsrewvc bnarv bdivrt.</p>
    <a class="read-link">Read More &raquo;</a>
  </div>
</section>

<section class="partners">
  <h2 class="section-title">Our Partners</h2>
  <div class="divider"><span></span></div>
  <svg class="partner-arrow" style="left:14px" width="24" height="44" viewBox="0 0 24 44"><path d="M20 2 4 22l16 20" stroke="#c5c8ce" stroke-width="2" fill="none"/></svg>
  <div class="partner-row">
    <div class="partner"><span></span></div>
    <div class="partner"><span></span></div>
    <div class="partner"><span></span></div>
    <div class="partner"><span></span></div>
    <div class="partner"><span></span></div>
    <div class="partner"><span></span></div>
  </div>
  <svg class="partner-arrow" style="left:1162px" width="24" height="44" viewBox="0 0 24 44"><path d="m4 2 16 20L4 42" stroke="#c5c8ce" stroke-width="2" fill="none"/></svg>
</section>

<footer class="site-footer">
  <svg class="footer-curve" width="1200" height="444" viewBox="0 0 1200 444"><path d="M0 100Q600 -40 1200 100V444H0z" fill="#d8dbe2"/><path d="M0 108Q600 -30 1200 108V444H0z" fill="var(--navy-deep)"/></svg>
  <div class="footer-seal"></div>
  <div class="footer-col quick-links">
    <h4>Quick Links</h4>
    <ul><li>Home</li><li>Properties</li><li>Virtual Tours &amp; Videos</li><li>Photos</li><li>Broker Referrals</li></ul>
  </div>
  <div class="col-sep" style="left:276px"></div>
  <div class="footer-col contact-col">
    <h4>Contact Details</h4>
    <ul>
      <li><svg width="13" height="16" viewBox="0 0 12 16"><path d="M6 0a6 6 0 0 0-6 6c0 4.5 6 10 6 10s6-5.5 6-10a6 6 0 0 0-6-6zm0 8.5A2.5 2.5 0 1 1 6 3.5a2.5 2.5 0 0 1 0 5z" fill="var(--orange)"/></svg><span><strong>CALLOWAY BUSINESS CENTERS</strong><br>4410 N. Harwood Avenue<br>Suite 300 , Dallas, Texas 75204</span></li>
      <li><svg width="14" height="14" viewBox="0 0 24 24"><path d="M6.6 10.8a15 15 0 0 0 6.6 6.6l2.2-2.2a1 1 0 0 1 1-.25 11.4 11.4 0 0 0 3.6.57 1 1 0 0 1 1 1V20a1 1 0 0 1-1 1A17 17 0 0 1 3 4a1 1 0 0 1 1-1h3.5a1 1 0 0 1 1 1c0 1.25.2 2.45.57 3.6a1 1 0 0 1-.25 1z" fill="var(--orange)"/></svg>+ 214.555.0147</li>
      <li><svg width="14" height="14" viewBox="0 0 24 24" fill="var(--orange)"><rect x="6" y="2" width="12" height="6"/><rect x="2" y="9" width="20" height="9" rx="2"/><rect x="6" y="15" width="12" height="7"/></svg>+ 214.555.0148</li>
      <li><svg width="14" height="12" viewBox="0 0 24 18"><rect width="24" height="18" rx="2" fill="var(--orange)"/><path d="m2 2 10 8 10-8" stroke="var(--navy-deep)" stroke-width="2" fill="none"/></svg>Offices@CallowayOffices.com</li>
    </ul>
  </div>
  <div class="col-sep" style="left:600px"></div>
  <div class="footer-col form-col">
    <h4>Quick Contact</h4>
    <form>
      <div class="field">Name</div>
      <div class="field">Email</div>
      <div class="field">Message</div>
      <div class="submit">Submit</div>
    </form>
  </div>
  <div class="col-sep" style="left:965px"></div>
  <div class="footer-col follow-col">
    <h4>Follow Us</h4>
    <ul>
      <li><span style="background:var(--red)"></span>PLUSLINE</li>
      <li><span style="background:var(--sky)"></span>CHIRPER</li>
      <li><span style="background:var(--blue)"></span>LINKWORK</li>
      <li><span style="background:#c8232c"></span>PINBOARD</li>
    </ul>
  </div>
  <div class="copyright">Copyright © 2016 Calloway Business Centers. All Rights Reserved.</div>
</footer>

</body>
</html>
```